Pre-workout label and Super Greens label for Brightmoor Nutrition Supplements

I need a label design for Club Brightmoor's 2 supplements. The first is a Pre-workout. The Pre-workout label needs to be 11.25 x 2.5 inches. This label will go on a black container. The second is a Super-Green. The Super-Green label should be 11.25 x 4.25 inches and will go on a white container. We have been selling these for a few years but the current labels are a little meh. I'd like something trendier and bolder. Must keep the Club Brightmoor branding. All the nurtition data must appear . I attached the current designs so you can know the flavors, nutrtional data etc. Thank you!
Updates

I can upload the Club Brightmoor logo! If anyone can tell me how to do that.

```html
<!DOCTYPE html>
<html lang="en">
<head>
<meta charset="UTF-8">
<title>Brightmoor Nutrition – Pre Workout Label</title>
<link rel="stylesheet" href="https://fonts.googleapis.com/css2?family=Barlow+Condensed:ital,wght@0,500;0,600;1,800&display=swap">
<style>
  :root {
    --page-bg: #f8f8f8;
    --red-light: #f0434a;
    --red: #d61d26;
    --red-deep: #a0060c;
    --black: #141414;
    --black-soft: #262626;
    --silver-light: #f2f2f2;
    --silver: #b9b9b9;
    --silver-dark: #7a7a7a;
    --flavor-red: #e8222c;
    --white: #ffffff;
    --ink-grey: #3a3a3a;
  }
  html, body {
    margin: 0;
    padding: 0;
    width: 1200px;
    height: 1131px;
    overflow: hidden;
    background: var(--page-bg);
  }
  .label {
    position: absolute;
    left: 100px;
    top: 140px;
    width: 1000px;
    height: 850px;
    display: block;
  }
  .brand-name {
    font-family: "Barlow Condensed", sans-serif;
    font-weight: 600;
    font-size: 34px;
    letter-spacing: 2px;
    fill: var(--white);
  }
  .product-title {
    font-family: "Barlow Condensed", sans-serif;
    font-style: italic;
    font-weight: 800;
    font-size: 112px;
    letter-spacing: 4px;
    fill: url(#titleSilver);
  }
  .flavor {
    font-family: "Barlow Condensed", sans-serif;
    font-style: italic;
    font-weight: 800;
    font-size: 56px;
    fill: var(--flavor-red);
  }
  .benefit-name {
    font-family: "Barlow Condensed", sans-serif;
    font-weight: 600;
    font-size: 27px;
    fill: var(--silver-light);
  }
  .benefit-note {
    font-family: "Barlow Condensed", sans-serif;
    font-weight: 500;
    font-size: 11px;
    letter-spacing: 1px;
    fill: var(--silver-dark);
  }
  .icon-ring { fill: none; stroke: var(--silver-light); stroke-width: 3.5; }
  .icon-mark { fill: var(--silver-light); }
  .tab-text {
    font-family: "Barlow Condensed", sans-serif;
    font-weight: 500;
    fill: var(--ink-grey);
  }
  .tab-title { font-size: 28px; }
  .tab-detail { font-size: 24px; }
</style>
</head>
<body>
<svg class="label" viewBox="0 0 1000 850" xmlns="http://www.w3.org/2000/svg" aria-label="Brightmoor Nutrition Pre Workout label, Watermelon Sugar">
  <defs>
    <linearGradient id="redField" x1="0" y1="0" x2="1" y2="0.3">
      <stop offset="0" stop-color="var(--red-light)"/>
      <stop offset="0.55" stop-color="var(--red)"/>
      <stop offset="1" stop-color="var(--red-deep)"/>
    </linearGradient>
    <linearGradient id="blackField" x1="0" y1="0" x2="1" y2="1">
      <stop offset="0" stop-color="var(--black-soft)"/>
      <stop offset="1" stop-color="var(--black)"/>
    </linearGradient>
    <linearGradient id="silverStripe" x1="0" y1="0" x2="1" y2="1">
      <stop offset="0" stop-color="var(--silver-dark)"/>
      <stop offset="0.5" stop-color="var(--silver-light)"/>
      <stop offset="1" stop-color="var(--silver)"/>
    </linearGradient>
    <linearGradient id="titleSilver" x1="0" y1="0" x2="0" y2="1">
      <stop offset="0" stop-color="#ffffff"/>
      <stop offset="0.55" stop-color="#d8d8d8"/>
      <stop offset="1" stop-color="#9d9d9d"/>
    </linearGradient>
    <linearGradient id="bottomBand" x1="0" y1="0" x2="1" y2="0">
      <stop offset="0" stop-color="var(--silver-dark)"/>
      <stop offset="0.5" stop-color="var(--silver-light)"/>
      <stop offset="1" stop-color="var(--silver-dark)"/>
    </linearGradient>
  </defs>

  <!-- red field -->
  <rect class="red-field" x="0" y="0" width="1000" height="850" fill="url(#redField)"/>

  <!-- black corner panel -->
  <polygon class="black-panel" points="0,198 0,850 870,850 818,812 0,812" fill="url(#blackField)"/>
  <polygon class="black-panel" points="0,198 818,812 0,812" fill="url(#blackField)"/>

  <!-- silver diagonal stripe -->
  <polygon class="silver-stripe" points="0,178 917,812 818,812 0,198" fill="url(#silverStripe)"/>

  <!-- bottom band -->
  <rect class="bottom-band" x="0" y="812" width="1000" height="38" fill="url(#bottomBand)"/>

  <!-- supplement info tab -->
  <polygon class="info-tab" points="312,758 682,758 712,850 282,850" fill="url(#bottomBand)"/>
  <text class="tab-text tab-title" x="497" y="797" text-anchor="middle">Dietary supplement</text>
  <text class="tab-text tab-detail" x="497" y="834" text-anchor="middle">30 Servings 240g (8.5oz)</text>

  <!-- brand -->
  <rect class="brand-square" x="498" y="124" width="26" height="26" fill="var(--white)"/>
  <text class="brand-name" x="511" y="207" text-anchor="middle">BRIGHTMOOR NUTRITION</text>

  <!-- product title -->
  <text class="product-title" x="494" y="390">PRE</text>
  <text class="product-title" x="494" y="490">WORKOUT</text>

  <!-- flavor -->
  <text class="flavor" x="218" y="642">WATERMELON</text>
  <text class="flavor" x="218" y="700">SUGAR</text>

  <!-- benefit: energy -->
  <g class="benefit benefit-energy">
    <circle class="icon-ring" cx="108" cy="375" r="29"/>
    <polygon class="icon-mark" points="113,352 96,379 107,379 102,398 121,369 110,369"/>
    <text class="benefit-name" x="108" y="436" text-anchor="middle">ENERGY</text>
    <text class="benefit-note" x="108" y="455" text-anchor="middle">CAFFEINE</text>
  </g>

  <!-- benefit: performance -->
  <g class="benefit benefit-performance">
    <circle class="icon-ring" cx="108" cy="525" r="29"/>
    <path class="icon-mark" d="M124,509 C112,509 100,518 96,530 L103,537 C115,533 124,521 124,509 Z M94,532 L88,538 L95,539 Z M101,539 L100,546 L106,540 Z"/>
    <text class="benefit-name" x="108" y="584" text-anchor="middle">PERFORMANCE</text>
    <text class="benefit-note" x="108" y="603" text-anchor="middle">BETA ALANINE</text>
  </g>

  <!-- benefit: strength -->
  <g class="benefit benefit-strength">
    <circle class="icon-ring" cx="108" cy="668" r="29"/>
    <rect class="icon-mark" x="88" y="656" width="6" height="24" rx="1"/>
    <rect class="icon-mark" x="96" y="660" width="5" height="16" rx="1"/>
    <rect class="icon-mark" x="101" y="666" width="14" height="4"/>
    <rect class="icon-mark" x="115" y="660" width="5" height="16" rx="1"/>
    <rect class="icon-mark" x="122" y="656" width="6" height="24" rx="1"/>
    <text class="benefit-name" x="108" y="732" text-anchor="middle">STRENGTH</text>
    <text class="benefit-note" x="108" y="750" text-anchor="middle">CREATINE</text>
  </g>
</svg>
</body>
</html>
```